Business Cards for new orthopaedic surgery practice

My husband and I are starting our own orthopaedic surgery practice. We are looking for a business card that is uniform, but one will have my name/title and the other will have his. You can just create one design with my name on it for now. But when I choose your design as the winning design I will ask that you add another copy with his name/title.

We are looking for classy, simple, elite all in one. We like dark blues/a little gold/yellow. Something that goes with our logo. We want our logo incorporated. Here is all the info you need:
Business name: RV Bone & Vitality Center
Location: 38517 North Willowmere Ave
Maple Hollow, FL 33958
Phone: 954-218-4063
Fax: 954-582-7341
Email: info@myrvbonecare.example

Names: Lydia Vance, M.D.
Board Certified Hand and Upper Extremity Surgeon

Ebo Dansu, M.D.
Board Certified Hip & Knee Replacement/General Orthopaedic Surgeon

Can decide what you want to put on the back. Maybe a slogan:
Grounded in Care. Built for You

I am just going to upload our logo. The only thing is if we select you as the winning design, the location, and phone numbers may change. We will need your help to update that once fully solidified.

Industry/Entity Type

Medical

Contact Information for Business Card

Colors
0054AA
0677BA
7BADD7
CADEEF
E8F1F8
0094D4
00A9DD
6FCCEA
C7EBF8
E9F6FB

Requirements
Must have
• class, appeal,
Should not have
• We want to air on the side of masculine if we are looking at masculine vs. feminine feel. But we still want it classy, sophisticated, and something we will love

```html
<!DOCTYPE html>
<html lang="en">
<head>
<meta charset="utf-8">
<title>RV Bone &amp; Vitality Center – Business Card</title>
<link rel="stylesheet" href="https://fonts.googleapis.com/css2?family=Montserrat:wght@400;600&display=swap">
<style>
  :root {
    --backdrop: #959595;
    --card: #ffffff;
    --navy: #253b82;
    --cyan: #16bde3;
    --ink: #333333;
    --on-band: #ffffff;
  }
  * { margin: 0; padding: 0; box-sizing: border-box; }
  html, body { width: 1200px; height: 1108px; overflow: hidden; }
  body {
    background: var(--backdrop);
    font-family: "Montserrat", sans-serif;
    color: var(--ink);
    position: relative;
  }
  .card {
    position: absolute;
    left: 242px;
    width: 715px;
    height: 409px;
    background: var(--card);
  }
  .card--front { top: 119px; }
  .card--back { top: 580px; }

  /* Front */
  .brand {
    position: absolute;
    inset: 0;
    display: flex;
    align-items: center;
    justify-content: center;
    gap: 18px;
  }
  .brand__dot {
    width: 40px; height: 40px;
    border-radius: 50%;
    background: var(--navy);
  }
  .brand__name {
    font-weight: 600;
    font-size: 34px;
    color: var(--navy);
    letter-spacing: 0.5px;
  }

  /* Back */
  .doctor { position: absolute; left: 0; right: 0; text-align: center; }
  .doctor__name {
    font-weight: 600;
    font-size: 31px;
    color: var(--cyan);
    line-height: 1;
  }
  .doctor__title {
    font-size: 16.5px;
    margin-top: 8px;
    line-height: 1;
  }
  .doctor--one { top: 88px; }
  .doctor--two { top: 168px; }

  .address {
    position: absolute;
    right: 368px;
    top: 245px;
    text-align: right;
    font-size: 17px;
    line-height: 27px;
    font-style: normal;
  }
  .address__practice { color: var(--cyan); }
  .contact-divider {
    position: absolute;
    left: 374px; top: 248px;
    width: 2px; height: 72px;
    background: var(--cyan);
  }
  .contacts {
    position: absolute;
    left: 402px;
    top: 245px;
    list-style: none;
    font-size: 17px;
    line-height: 27px;
  }
  .contacts li { display: flex; align-items: center; gap: 8px; }
  .contacts svg { width: 16px; height: 16px; fill: var(--cyan); flex: none; }
  .tagline {
    position: absolute;
    left: 0; right: 0;
    top: 358px;
    height: 25px;
    background: var(--cyan);
    color: var(--on-band);
    font-size: 16.5px;
    text-align: center;
    line-height: 25px;
  }
</style>
</head>
<body>
  <section class="card card--front">
    <div class="brand">
      <span class="brand__dot"></span>
      <span class="brand__name">RV Bone &amp; Vitality Center</span>
    </div>
  </section>

  <section class="card card--back">
    <div class="doctor doctor--one">
      <p class="doctor__name">Lydia Vance, M.D.</p>
      <p class="doctor__title">Board Certified Hand and Upper Extremity Surgeon</p>
    </div>
    <div class="doctor doctor--two">
      <p class="doctor__name">Ebo Dansu, M.D.</p>
      <p class="doctor__title">Board Certified Hip &amp; Knee Replacement/General Orthopaedic Surgeon</p>
    </div>

    <address class="address">
      <div class="address__practice">RV Orthopaedic Specialists</div>
      <div>38517 North Willowmere Ave</div>
      <div>Maple Hollow, FL 33958</div>
    </address>
    <div class="contact-divider"></div>
    <ul class="contacts">
      <li>
        <svg viewBox="0 0 16 16" aria-hidden="true"><path d="M1 6c0-2 3-3 7-3s7 1 7 3v1h-3V6H4v1H1z"/><rect x="3" y="8" width="10" height="6" rx="1"/></svg>
        954-218-4063
      </li>
      <li>
        <svg viewBox="0 0 16 16" aria-hidden="true"><rect x="4" y="1" width="8" height="4"/><rect x="1" y="5" width="14" height="6" rx="1"/><rect x="4" y="9" width="8" height="6" fill="#fff" stroke="#16bde3" stroke-width="1.5"/></svg>
        954-582-7341
      </li>
      <li>
        <svg viewBox="0 0 16 16" aria-hidden="true"><path d="M1 4h14v9H1z"/><path d="M1 4l7 5 7-5" fill="none" stroke="#fff" stroke-width="1.2"/></svg>
        info@myrvbonecare.example
      </li>
    </ul>

    <p class="tagline">Grounded in Care. Built for You</p>
  </section>
</body>
</html>
```